RWT Fittings Ltd Business Cards

We need a business card with our business logo. We provide window and door installations on high-rises in west coast British Colombia, Canada.

I would like my business information and details on one side of the card, and the other side the company name with logo

Target Market(s)

General Contractors

Industry/Entity Type

Construction

Contact Information for Business Card

one side i want my company name and logo in the dark theme logo that i provided

Requirements
Must have
• Marco Peltieri, 16045518293, RWTFittings@mailbox-demo.com, 1407-5194 Linden Row Burnaby BC, V5H 2K9, Owner & Manager

```html
<!DOCTYPE html>
<html lang="en">
<head>
<meta charset="utf-8">
<title>RWT Fittings Ltd – Business Cards</title>
<link rel="stylesheet" href="https://fonts.googleapis.com/css2?family=Poppins:wght@600;700&family=Roboto:wght@400;500&display=swap">
<style>
  :root {
    --backdrop: #232323;
    --card: #2a2724;
    --card-deep: #221f1c;
    --band-1: #2e2b28;
    --band-2: #34312d;
    --accent: #29a9e1;
    --grey-name: #a6a29c;
    --ink: #f2f2f2;
  }
  * { margin: 0; padding: 0; box-sizing: border-box; }
  html, body { width: 1200px; height: 780px; overflow: hidden; }
  body {
    background: var(--backdrop);
    font-family: "Roboto", Arial, sans-serif;
    position: relative;
  }
  .card {
    position: absolute;
    top: 58px;
    width: 380px;
    height: 664px;
    border-radius: 22px;
    overflow: hidden;
    box-shadow: 0 14px 34px rgba(0,0,0,.55);
  }
  /* Front side */
  .card--front { left: 190px; background: var(--card-deep); }
  .front-photo {
    position: absolute; inset: 0;
    background:
      radial-gradient(ellipse at 40% 25%, rgba(120,112,104,.45), transparent 60%),
      linear-gradient(180deg, #4a4540 0%, #34302c 45%, #24211e 100%);
  }
  .front-name {
    position: absolute;
    left: 50%; top: 50%;
    transform: translate(-50%, -50%) rotate(-90deg);
    white-space: nowrap;
    font-family: "Poppins", Arial, sans-serif;
    font-weight: 700;
    font-size: 46px;
    color: var(--accent);
    letter-spacing: .5px;
  }
  /* Back side */
  .card--back { left: 630px; background: var(--card); }
  .back-curves { position: absolute; inset: 0; }
  .back-brand {
    position: absolute; top: 74px; left: 0; right: 0;
    text-align: center;
    font-family: "Poppins", Arial, sans-serif;
    font-weight: 700;
    font-size: 32px;
    color: var(--accent);
  }
  .contact-block {
    position: absolute; top: 262px; left: 0; right: 0;
    text-align: center;
  }
  .person-name {
    font-family: "Poppins", Arial, sans-serif;
    font-weight: 700;
    font-size: 30px;
    line-height: 1.1;
  }
  .person-name .first { color: var(--accent); }
  .person-name .last { color: var(--grey-name); }
  .person-title {
    font-family: "Poppins", Arial, sans-serif;
    font-weight: 600;
    font-size: 14px;
    color: var(--ink);
    margin-top: 2px;
  }
  .contact-icons {
    display: flex; justify-content: center; gap: 12px;
    margin-top: 12px;
  }
  .icon-dot {
    width: 26px; height: 26px; border-radius: 50%;
    background: var(--accent);
    display: flex; align-items: center; justify-content: center;
  }
  .contact-line {
    font-size: 14px; color: var(--ink);
    margin-top: 8px; letter-spacing: .2px;
  }
  .contact-line + .contact-line { margin-top: 3px; }
  .address-block {
    position: absolute; top: 520px; left: 0; right: 0;
    text-align: center;
  }
  .address-block .icon-dot { margin: 0 auto 10px; }
  .address-line { font-size: 14px; color: var(--ink); line-height: 1.35; }
</style>
</head>
<body>

<section class="card card--front">
  <div class="front-photo" role="img" aria-label="Faint photo of a bright interior with tall windows and a plant"></div>
  <div class="front-name">RWT Fittings Ltd</div>
</section>

<section class="card card--back">
  <svg class="back-curves" width="380" height="664" viewBox="0 0 380 664" aria-hidden="true">
    <path d="M0 460 Q120 420 240 470 T380 440 V664 H0 Z" fill="var(--band-1)"/>
    <path d="M0 300 Q0 480 200 480 Q340 480 380 330 V400 Q300 520 170 500 Q40 480 0 560 Z" fill="var(--band-2)" opacity=".55"/>
    <path d="M0 560 Q60 500 170 500 Q300 500 380 400 V664 H0 Z" fill="var(--band-1)"/>
  </svg>

  <div class="back-brand">RWT Fittings Ltd</div>

  <div class="contact-block">
    <div class="person-name"><span class="first">Marco</span> <span class="last">Peltieri</span></div>
    <div class="person-title">Owner &amp; Manager</div>
    <div class="contact-icons">
      <span class="icon-dot">
        <svg width="14" height="14" viewBox="0 0 24 24" aria-label="Phone"><path fill="#fff" d="M6.6 10.8a15 15 0 0 0 6.6 6.6l2.2-2.2c.3-.3.7-.4 1-.2 1.1.4 2.3.6 3.6.6.6 0 1 .4 1 1V20c0 .6-.4 1-1 1A17 17 0 0 1 3 4c0-.6.4-1 1-1h3.5c.6 0 1 .4 1 1 0 1.3.2 2.5.6 3.6.1.3 0 .7-.2 1z"/></svg>
      </span>
      <span class="icon-dot">
        <svg width="14" height="14" viewBox="0 0 24 24" aria-label="Email"><path fill="#fff" d="M3 5h18v14H3z"/><path d="M3 5l9 7 9-7" fill="none" stroke="#29a9e1" stroke-width="2"/></svg>
      </span>
    </div>
    <div class="contact-line">1604 551 8293</div>
    <div class="contact-line">RWTFittings@mailbox-demo.com</div>
  </div>

  <div class="address-block">
    <span class="icon-dot">
      <svg width="14" height="14" viewBox="0 0 24 24" aria-label="Location"><path fill="#fff" d="M12 2a7 7 0 0 0-7 7c0 5 7 13 7 13s7-8 7-13a7 7 0 0 0-7-7zm0 9.5A2.5 2.5 0 1 1 12 6.5a2.5 2.5 0 0 1 0 5z"/></svg>
    </span>
    <div class="address-line">1407-5194 Linden Row</div>
    <div class="address-line">Burnaby BC, V5H 2K9</div>
  </div>
</section>

</body>
</html>
```